Professional Website

We are looking for a new website for our Staffing Company. Attached is a document with all the details and pages needed along with some examples of others websites.

We want a professional Look and feel around the same color theme as the attached Amber Compass.

We currently host our site on PageLoom.io. If the winning designer can also add to PageLoom, that is a plus.

```html
<!DOCTYPE html>
<html lang="en">
<head>
<meta charset="utf-8">
<title>Crewpoint – Clerical & Industrial Staffing</title>
<link href="https://fonts.googleapis.com/css2?family=Ubuntu:wght@400;500;700&family=Lato:wght@400;700&display=swap" rel="stylesheet">
<style>
:root{
  --blue:#2b36ad;
  --blue-dark:#232c93;
  --ink:#1d1d24;
  --body:#4a4a55;
  --muted:#f4f4f6;
  --line:#e3e4ea;
  --black:#000;
  --board:#5f5f5f;
  --white:#fff;
}
*{box-sizing:border-box;margin:0;padding:0}
html,body{width:757px;height:1200px;overflow:hidden;background:var(--board)}
body{font-family:"Lato",sans-serif;color:var(--body)}
h1,h2,h3,h4{font-weight:400}
.board{position:absolute;left:0;top:0;width:1518px;height:2408px;transform:scale(.4987);transform-origin:0 0;background:var(--board)}
.page{position:absolute;width:687px;background:var(--white);overflow:hidden}
.page--home{left:48px;top:40px;height:2327px}
.page--inner{left:783px;top:40px;height:908px}

/* header */
.topbar{position:absolute;left:0;top:0;width:687px;height:43px;background:var(--white)}
.brand{position:absolute;left:64px;top:6px;font-family:"Ubuntu",sans-serif;font-weight:700;font-size:27px;color:var(--blue);letter-spacing:-.5px}
.topbar__phone{position:absolute;left:264px;top:15px;font-size:10px;color:var(--blue);display:flex;gap:6px;align-items:center}
.topbar__logins{position:absolute;left:368px;top:10px;display:flex;gap:5px}
.pill{background:var(--blue);color:var(--white);font-family:"Ubuntu",sans-serif;font-weight:500;font-size:8.5px;border-radius:12px;height:22px;padding:0 10px;display:flex;align-items:center}
.navbar{position:absolute;left:0;top:43px;width:687px;height:34px;background:var(--blue);display:flex;align-items:center;padding-left:206px;font-family:"Ubuntu",sans-serif;font-size:8.5px;color:var(--white)}
.navbar__item{margin-right:40px}
.navbar__social{display:flex;gap:19px;align-items:center;margin-left:-5px}
.dot-icon{width:8px;height:8px;border-radius:50%;background:var(--white)}

/* hero */
.hero{position:absolute;left:0;top:77px;width:687px;height:344px}
.hero__photo{position:absolute;inset:0;background:linear-gradient(100deg,#b9b3ad 0%,#d6d1ca 35%,#c9bfb8 55%,#8c929b 78%,#2f3440 100%)}
.hero__title{position:absolute;left:64px;top:60px;font-family:"Ubuntu",sans-serif;font-weight:700;font-size:21px;line-height:34.5px;color:var(--white);letter-spacing:.6px;text-shadow:0 1px 3px rgba(0,0,0,.3)}
.hero__cta{position:absolute;left:64px;top:171px;display:flex;gap:8px}
.btn{font-family:"Ubuntu",sans-serif;font-weight:500;font-size:8px;border-radius:15px;height:29px;padding:0 11px;display:flex;align-items:center;white-space:nowrap}
.btn--solid{background:var(--blue);color:var(--white)}
.btn--ghost{border:1.5px solid var(--blue);color:var(--blue);background:rgba(255,255,255,.35)}
.btn--light{background:var(--white);color:var(--blue)}
.hero__dots{position:absolute;left:331px;top:320px;display:flex;gap:4px;align-items:center}
.hero__dots span{width:5px;height:5px;border-radius:50%;background:var(--white)}
.hero__dots .on{width:8px;height:8px;border:2px solid var(--white);background:var(--blue)}

/* welcome */
.welcome{position:absolute;left:0;top:421px;width:687px;height:251px}
.texture{position:absolute;background:#f1f2f7}
.section-title{font-family:"Ubuntu",sans-serif;font-weight:500;font-size:16.5px;color:var(--ink);text-align:center}
.welcome .section-title{position:absolute;left:0;right:0;top:46px}
.welcome__text{position:absolute;left:122px;width:443px;top:82px;font-size:8.6px;line-height:14.8px;text-align:center}
.welcome .btn{position:absolute;left:306px;top:172px;padding:0 15px}

/* jobs */
.jobs{position:absolute;left:0;top:672px;width:687px;height:353px;background:var(--muted)}
.jobs .section-title{position:absolute;left:0;right:0;top:45px}
.jobs__lead{position:absolute;left:150px;width:387px;top:73px;font-size:8.6px;line-height:14.5px;text-align:center}
.job-card{position:absolute;top:122px;width:132px;height:181px;background:var(--white);box-shadow:0 1px 4px rgba(0,0,0,.06);text-align:center}
.job-card__icon{position:absolute;left:37px;top:15px;width:58px;height:58px;border-radius:50%;border:1.5px solid var(--blue);background:var(--white)}
.job-card__icon--active{background:var(--blue)}
.job-card__title{position:absolute;left:0;right:0;top:89px;font-family:"Ubuntu",sans-serif;font-weight:400;font-size:11.5px;color:var(--ink)}
.job-card__desc{position:absolute;left:10px;right:10px;top:112px;font-size:7px;line-height:12px}
.apply{font-family:"Ubuntu",sans-serif;font-weight:500;font-size:8px;color:var(--blue)}
.job-card .apply{position:absolute;left:0;right:0;top:156px}

/* offices */
.offices{position:absolute;left:0;top:1025px;width:687px;height:409px}
.offices .section-title{position:absolute;left:0;right:0;top:45px}
.office{position:absolute;top:90px;width:177px;height:270px}
.office__photo{position:absolute;left:0;top:0;width:177px;height:160px}
.office__panel{position:absolute;left:10px;top:125px;width:157px;height:143px;background:var(--white);clip-path:polygon(0 35px,100% 0,100% 100%,0 100%);border-bottom:2px solid var(--blue)}
.office__city{position:absolute;left:31px;top:40px;font-family:"Ubuntu",sans-serif;font-weight:500;font-size:11px;color:var(--ink)}
.office__row{position:absolute;left:31px;font-size:8px;line-height:14.5px;color:var(--body);display:flex;gap:9px}
.office__row svg{flex:none;margin-top:3px}
.office .apply{position:absolute;left:31px;top:124px}
.arrow{position:absolute;top:156px;width:31px;height:31px;border-radius:50%;display:flex;align-items:center;justify-content:center;box-shadow:0 1px 5px rgba(0,0,0,.15)}
.arrow--prev{left:24px;background:var(--white)}
.arrow--next{left:634px;background:var(--blue)}

/* about */
.about{position:absolute;left:0;top:1434px;width:687px;height:319px;background:linear-gradient(120deg,#3540b4 0%,#2a349f 55%,#2f3aa8 100%);color:var(--white)}
.about h3{position:absolute;left:64px;font-family:"Ubuntu",sans-serif;font-weight:500;font-size:16.5px}
.about p{position:absolute;left:64px;width:285px;font-size:8.6px;line-height:14.8px;color:#e7e9ff}
.about .btn{position:absolute;left:65px;top:227px;padding:0 15px}
.about__photo{position:absolute;left:377px;top:54px;width:251px;height:215px;border-radius:26px;border:2px solid rgba(255,255,255,.8);background:linear-gradient(110deg,#c7ccd6 0%,#8e96a6 45%,#4a6a98 80%,#2e4c7e 100%)}

/* question */
.question{position:absolute;left:0;top:1753px;width:687px;height:340px}
.question h3{position:absolute;left:64px;top:44px;font-family:"Ubuntu",sans-serif;font-weight:500;font-size:23px;line-height:32px;color:var(--ink)}
.question__note{position:absolute;left:64px;top:125px;width:140px;font-size:8.4px;line-height:14.8px}
.question__note b{color:var(--ink)}
.field{position:absolute;border:1px solid var(--line);background:#fbfbfc;font-size:8.4px;color:#8b8c96;padding:12px 14px}
.question .btn{position:absolute;left:225px;top:303px;padding:0 24px}

/* footer */
.footer{position:absolute;left:0;width:687px;height:235px;background:var(--black);color:var(--white)}
.page--home .footer{top:2093px}
.page--inner .footer{top:672px}
.footer .brand{left:63px;top:40px;font-size:25px;color:var(--white)}
.footer__about{position:absolute;left:63px;top:96px;width:135px;font-size:8px;line-height:15px}
.footer__col{position:absolute;top:52px;font-size:8.4px;line-height:14.7px}
.footer__col h4{font-family:"Ubuntu",sans-serif;font-weight:500;font-size:9px;margin-bottom:12px}
.footer__contact li{display:flex;gap:9px;margin-bottom:8px;list-style:none}
.footer__contact svg{flex:none;margin-top:2px}
.footer__col ul{list-style:none}
.social-link{display:flex;align-items:center;gap:10px;margin-bottom:8px}
.social-link span{width:25px;height:25px;border-radius:50%;border:1.5px solid var(--white);display:block}
.footer__rule{position:absolute;left:63px;right:63px;top:186px;border-top:1px solid #222}
.footer__copy{position:absolute;left:0;right:0;top:206px;text-align:center;font-size:8.4px}
</style>
</head>
<body>
<div class="board">

<section class="page page--home">
  <header class="topbar">
    <div class="brand">Crewpoint</div>
    <div class="topbar__phone"><svg width="9" height="9" viewBox="0 0 24 24"><path fill="#2b36ad" d="M6.6 10.8c1.4 2.8 3.8 5.1 6.6 6.6l2.2-2.2c.3-.3.7-.4 1-.2 1.1.4 2.3.6 3.6.6.6 0 1 .4 1 1V20c0 .6-.4 1-1 1C10.6 21 3 13.4 3 4c0-.6.4-1 1-1h3.5c.6 0 1 .4 1 1 0 1.3.2 2.5.6 3.6.1.3 0 .7-.2 1l-2.3 2.2z"/></svg>555-014-0100</div>
    <div class="topbar__logins"><span class="pill">Employee Login</span><span class="pill">Swift Card Login</span><span class="pill">Payroll Login</span></div>
  </header>
  <nav class="navbar">
    <span class="navbar__item">HOME</span><span class="navbar__item">JOBS ▾</span><span class="navbar__item">ABOUT US</span><span class="navbar__item">CONTACT US</span>
    <span class="navbar__social"><i class="dot-icon"></i><i class="dot-icon"></i><i class="dot-icon"></i>
      <svg width="10" height="10" viewBox="0 0 24 24"><circle cx="10" cy="10" r="7" fill="none" stroke="#fff" stroke-width="3"/><path d="M15 15l6 6" stroke="#fff" stroke-width="3"/></svg></span>
  </nav>
  <div class="hero">
    <div class="hero__photo" role="img" aria-label="Recruiter smiling across a desk during an interview with a candidate"></div>
    <h1 class="hero__title">RECRUITING AGENCY FOR<br>TEMPORARY AND DIRECT<br>HIRE EMPLOYEES</h1>
    <div class="hero__cta"><span class="btn btn--solid">I'm looking for a Job</span><span class="btn btn--ghost">I need Employees</span></div>
    <div class="hero__dots"><span></span><span class="on"></span><span></span></div>
  </div>
  <div class="welcome">
    <div class="texture" role="img" aria-label="Dotted accent" style="left:4px;top:3px;width:60px;height:108px"></div>
    <div class="texture" role="img" aria-label="Dotted accent" style="left:626px;top:140px;width:60px;height:108px"></div>
    <h2 class="section-title">Welcome To</h2>
    <p class="welcome__text">Greatest part of our daily job is that we are constantly bringing people together. Our Clients come to us in search of the perfect candidate and the job hunters approach us when they are in need of a job or looking for their next exciting role. Being able to work with and connect the two is incredibly satisfying. Not to mention that in today's current job market, employers are fighting for the top talent. This makes our employees and partners grateful for the help in finding it!</p>
    <span class="btn btn--solid">Learn More</span>
  </div>
  <div class="jobs">
    <h2 class="section-title">Jobs Panel</h2>
    <p class="jobs__lead">Are you tired of jumping from one temporary staffing agency to the next? At Crewpoint, we provide great pay, PTO/Vacation pay, and much more.</p>
    <div class="job-card" style="left:64px"><div class="job-card__icon" role="img" aria-label="Welder icon"></div><h3 class="job-card__title">Welders</h3><p class="job-card__desc">We are hiring for, a reputed metal display company located in Hammond, IN...</p><span class="apply">Apply Now →</span></div>
    <div class="job-card" style="left:206px"><div class="job-card__icon job-card__icon--active" role="img" aria-label="Material handler icon"></div><h3 class="job-card__title">Material Handlers</h3><p class="job-card__desc">You will be expected to work with a team and efficiently coordinate with them...</p><span class="apply">Apply Now →</span></div>
    <div class="job-card" style="left:349px"><div class="job-card__icon" role="img" aria-label="General labourer icon"></div><h3 class="job-card__title">General Labour</h3><p class="job-card__desc">Hiring general labor is our focus and we help the right persons get employed...</p><span class="apply">Apply Now →</span></div>
    <div class="job-card" style="left:491px"><div class="job-card__icon" role="img" aria-label="Forklift icon"></div><h3 class="job-card__title">Forklift Driver</h3><p class="job-card__desc">As a forklift operator, you will be required to move packages and materials...</p><span class="apply">Apply Now →</span></div>
  </div>
  <div class="offices">
    <h2 class="section-title">Contact Us</h2>
    <div class="arrow arrow--prev"><svg width="12" height="8" viewBox="0 0 12 8"><path d="M11 4H1M4 1L1 4l3 3" fill="none" stroke="#2b36ad" stroke-width="1.2"/></svg></div>
    <div class="arrow arrow--next"><svg width="12" height="8" viewBox="0 0 12 8"><path d="M1 4h10M8 1l3 3-3 3" fill="none" stroke="#fff" stroke-width="1.2"/></svg></div>
    <div class="office" style="left:64px">
      <div class="office__photo" role="img" aria-label="City skyline at sunset" style="background:linear-gradient(160deg,#c9a3c8 0%,#e7b9a6 45%,#8a6c6a 80%,#4a4a55 100%)"></div>
      <div class="office__panel"><h3 class="office__city">Chicago, IL</h3>
        <div class="office__row" style="top:60px"><svg width="7" height="9" viewBox="0 0 10 14"><path d="M5 0a5 5 0 00-5 5c0 4 5 9 5 9s5-5 5-9a5 5 0 00-5-5zm0 7a2 2 0 110-4 2 2 0 010 4z" fill="#2b36ad"/></svg><span>410 Lakeview Ave.<br>Chicago, IL 60600</span></div>
        <div class="office__row" style="top:95px"><svg width="8" height="8" viewBox="0 0 24 24"><path fill="#2b36ad" d="M6.6 10.8c1.4 2.8 3.8 5.1 6.6 6.6l2.2-2.2c.3-.3.7-.4 1-.2 1.1.4 2.3.6 3.6.6.6 0 1 .4 1 1V20c0 .6-.4 1-1 1C10.6 21 3 13.4 3 4c0-.6.4-1 1-1h3.5c.6 0 1 .4 1 1 0 1.3.2 2.5.6 3.6.1.3 0 .7-.2 1z"/></svg><span>555-014-0200</span></div>
        <span class="apply">Apply Now →</span></div>
    </div>
    <div class="office" style="left:255px">
      <div class="office__photo" role="img" aria-label="Historic stone buildings among trees" style="background:linear-gradient(170deg,#9fb6d3 0%,#8c8577 45%,#5f5a4c 100%)"></div>
      <div class="office__panel"><h3 class="office__city">Hammond, IN</h3>
        <div class="office__row" style="top:60px"><svg width="7" height="9" viewBox="0 0 10 14"><path d="M5 0a5 5 0 00-5 5c0 4 5 9 5 9s5-5 5-9a5 5 0 00-5-5zm0 7a2 2 0 110-4 2 2 0 010 4z" fill="#2b36ad"/></svg><span>228 Riverside Blvd.<br>Hammond, IN 46300</span></div>
        <div class="office__row" style="top:95px"><svg width="8" height="8" viewBox="0 0 24 24"><path fill="#2b36ad" d="M6.6 10.8c1.4 2.8 3.8 5.1 6.6 6.6l2.2-2.2c.3-.3.7-.4 1-.2 1.1.4 2.3.6 3.6.6.6 0 1 .4 1 1V20c0 .6-.4 1-1 1C10.6 21 3 13.4 3 4c0-.6.4-1 1-1h3.5c.6 0 1 .4 1 1 0 1.3.2 2.5.6 3.6.1.3 0 .7-.2 1z"/></svg><span>555-014-0300</span></div>
        <span class="apply">Apply Now →</span></div>
    </div>
    <div class="office" style="left:446px">
      <div class="office__photo" role="img" aria-label="Coastal town on green hills" style="background:linear-gradient(170deg,#a9bcd6 0%,#4c6a52 45%,#7a6a5a 80%,#5b6e5a 100%)"></div>
      <div class="office__panel"><h3 class="office__city">Alsip, IL</h3>
        <div class="office__row" style="top:60px"><svg width="7" height="9" viewBox="0 0 10 14"><path d="M5 0a5 5 0 00-5 5c0 4 5 9 5 9s5-5 5-9a5 5 0 00-5-5zm0 7a2 2 0 110-4 2 2 0 010 4z" fill="#2b36ad"/></svg><span>905 Maple Row<br>Blue Island, IL 60400</span></div>
        <div class="office__row" style="top:95px"><svg width="8" height="8" viewBox="0 0 24 24"><path fill="#2b36ad" d="M6.6 10.8c1.4 2.8 3.8 5.1 6.6 6.6l2.2-2.2c.3-.3.7-.4 1-.2 1.1.4 2.3.6 3.6.6.6 0 1 .4 1 1V20c0 .6-.4 1-1 1C10.6 21 3 13.4 3 4c0-.6.4-1 1-1h3.5c.6 0 1 .4 1 1 0 1.3.2 2.5.6 3.6.1.3 0 .7-.2 1z"/></svg><span>555-014-0100</span></div>
        <span class="apply">Apply Now →</span></div>
    </div>
  </div>
  <div class="about">
    <h3 style="top:60px">About Crewpoint</h3>
    <p style="top:90px">Are you tired of the average temporary staffing agency that sends unqualified warm bodies? We're the first and only recruiting agency specializing in long-term temporary and direct hire staffing.</p>
    <h3 style="top:150px">Our Mission</h3>
    <p style="top:179px">To change the way temporary staffing agencies fill orders. We only work with the best companies and best employees.</p>
    <span class="btn btn--light">Learn More</span>
    <div class="about__photo" role="img" aria-label="Smiling businessman meeting a client at an office table"></div>
  </div>
  <div class="question">
    <h3>Got a<br>question?</h3>
    <p class="question__note">We're here to help. Send us an email or call us at <b>555-014-0200</b></p>
    <div class="field" style="left:224px;top:89px;width:195px;height:34px">First Name</div>
    <div class="field" style="left:430px;top:89px;width:194px;height:34px">Last Name</div>
    <div class="field" style="left:224px;top:133px;width:400px;height:34px">Phone</div>
    <div class="field" style="left:224px;top:178px;width:400px;height:34px">Email Address</div>
    <div class="field" style="left:224px;top:222px;width:400px;height:67px">Tell me something about You*</div>
    <span class="btn btn--solid">Submit</span>
  </div>
  <footer class="footer">
    <div class="brand">Crewpoint</div>
    <p class="footer__about">Greatest part of our daily job is that we are constantly bringing people together.</p>
    <div class="footer__col" style="left:213px"><h4>Quick Links</h4><ul><li>Home</li><li>About</li><li>Pricing</li><li>FAQs</li><li>Contact</li></ul></div>
    <div class="footer__col" style="left:297px"><h4>Areas we service</h4><ul><li>Blue Island</li><li>Alsip</li><li>Romeoville</li></ul></div>
    <div class="footer__col footer__contact" style="left:404px"><h4>contact us</h4><ul>
      <li><svg width="8" height="10" viewBox="0 0 10 14"><path d="M5 0a5 5 0 00-5 5c0 4 5 9 5 9s5-5 5-9a5 5 0 00-5-5zm0 7a2 2 0 110-4 2 2 0 010 4z" fill="#fff"/></svg><span>Lorem ipsum dolor sit<br>amet, consectetur</span></li>
      <li><svg width="8" height="8" viewBox="0 0 24 24"><path fill="#fff" d="M6.6 10.8c1.4 2.8 3.8 5.1 6.6 6.6l2.2-2.2c.3-.3.7-.4 1-.2 1.1.4 2.3.6 3.6.6.6 0 1 .4 1 1V20c0 .6-.4 1-1 1C10.6 21 3 13.4 3 4c0-.6.4-1 1-1h3.5c.6 0 1 .4 1 1 0 1.3.2 2.5.6 3.6.1.3 0 .7-.2 1z"/></svg><span>555-014-0100</span></li>
      <li><svg width="9" height="7" viewBox="0 0 18 13"><rect width="18" height="13" fill="#fff"/><path d="M0 0l9 7 9-7" fill="none" stroke="#000" stroke-width="1.5"/></svg><span>hello@crewpointstaff.com</span></li></ul></div>
    <div class="footer__col" style="left:548px"><h4>social</h4>
      <div class="social-link"><span></span>Community</div><div class="social-link"><span></span>Updates</div><div class="social-link"><span></span>Network</div></div>
    <div class="footer__rule"></div>
    <p class="footer__copy">©Copyrights 2022 Crewpoint Staffing &nbsp;| &nbsp; All Rights Reserved</p>
  </footer>
</section>

<section class="page page--inner">
  <header class="topbar">
    <div class="brand">Crewpoint</div>
    <div class="topbar__phone"><svg width="9" height="9" viewBox="0 0 24 24"><path fill="#2b36ad" d="M6.6 10.8c1.4 2.8 3.8 5.1 6.6 6.6l2.2-2.2c.3-.3.7-.4 1-.2 1.1.4 2.3.6 3.6.6.6 0 1 .4 1 1V20c0 .6-.4 1-1 1C10.6 21 3 13.4 3 4c0-.6.4-1 1-1h3.5c.6 0 1 .4 1 1 0 1.3.2 2.5.6 3.6.1.3 0 .7-.2 1l-2.3 2.2z"/></svg>555-014-0100</div>
    <div class="topbar__logins"><span class="pill">Employee Login</span><span class="pill">Swift Card Login</span><span class="pill">Payroll Login</span></div>
  </header>
  <nav class="navbar">
    <span class="navbar__item">HOME</span><span class="navbar__item">JOBS ▾</span><span class="navbar__item">ABOUT US</span><span class="navbar__item">CONTACT US</span>
    <span class="navbar__social"><i class="dot-icon"></i><i class="dot-icon"></i><i class="dot-icon"></i>
      <svg width="10" height="10" viewBox="0 0 24 24"><circle cx="10" cy="10" r="7" fill="none" stroke="#fff" stroke-width="3"/><path d="M15 15l6 6" stroke="#fff" stroke-width="3"/></svg></span>
  </nav>
  <div class="hero">
    <div class="hero__photo" role="img" aria-label="Recruiter smiling across a desk during an interview with a candidate"></div>
    <h1 class="hero__title">RECRUITING AGENCY FOR<br>TEMPORARY AND DIRECT<br>HIRE EMPLOYEES</h1>
    <div class="hero__cta"><span class="btn btn--solid">I'm looking for a Job</span><span class="btn btn--ghost">I need Employees</span></div>
    <div class="hero__dots"><span></span><span class="on"></span><span></span></div>
  </div>
  <div class="welcome">
    <div class="texture" role="img" aria-label="Dotted accent" style="left:4px;top:3px;width:60px;height:108px"></div>
    <div class="texture" role="img" aria-label="Dotted accent" style="left:626px;top:140px;width:60px;height:108px"></div>
    <h2 class="section-title">Welcome To</h2>
    <p class="welcome__text">Greatest part of our daily job is that we are constantly bringing people together. Our Clients come to us in search of the perfect candidate and the job hunters approach us when they are in need of a job or looking for their next exciting role. Being able to work with and connect the two is incredibly satisfying. Not to mention that in today's current job market, employers are fighting for the top talent. This makes our employees and partners grateful for the help in finding it!</p>
    <span class="btn btn--solid">Learn More</span>
  </div>
  <footer class="footer">
    <div class="brand">Crewpoint</div>
    <p class="footer__about">Greatest part of our daily job is that we are constantly bringing people together.</p>
    <div class="footer__col" style="left:213px"><h4>Quick Links</h4><ul><li>Home</li><li>About</li><li>Pricing</li><li>FAQs</li><li>Contact</li></ul></div>
    <div class="footer__col" style="left:297px"><h4>Areas we service</h4><ul><li>Blue Island</li><li>Alsip</li><li>Romeoville</li></ul></div>
    <div class="footer__col footer__contact" style="left:404px"><h4>contact us</h4><ul>
      <li><svg width="8" height="10" viewBox="0 0 10 14"><path d="M5 0a5 5 0 00-5 5c0 4 5 9 5 9s5-5 5-9a5 5 0 00-5-5zm0 7a2 2 0 110-4 2 2 0 010 4z" fill="#fff"/></svg><span>Lorem ipsum dolor sit<br>amet, consectetur</span></li>
      <li><svg width="8" height="8" viewBox="0 0 24 24"><path fill="#fff" d="M6.6 10.8c1.4 2.8 3.8 5.1 6.6 6.6l2.2-2.2c.3-.3.7-.4 1-.2 1.1.4 2.3.6 3.6.6.6 0 1 .4 1 1V20c0 .6-.4 1-1 1C10.6 21 3 13.4 3 4c0-.6.4-1 1-1h3.5c.6 0 1 .4 1 1 0 1.3.2 2.5.6 3.6.1.3 0 .7-.2 1z"/></svg><span>555-014-0100</span></li>
      <li><svg width="9" height="7" viewBox="0 0 18 13"><rect width="18" height="13" fill="#fff"/><path d="M0 0l9 7 9-7" fill="none" stroke="#000" stroke-width="1.5"/></svg><span>hello@crewpointstaff.com</span></li></ul></div>
    <div class="footer__col" style="left:548px"><h4>social</h4>
      <div class="social-link"><span></span>Community</div><div class="social-link"><span></span>Updates</div><div class="social-link"><span></span>Network</div></div>
    <div class="footer__rule"></div>
    <p class="footer__copy">©Copyrights 2022 Crewpoint Staffing &nbsp;| &nbsp; All Rights Reserved</p>
  </footer>
</section>

</div>
</body>
</html>
```